New business card for a regional office of a US M&A company

We need business card for a finance company, office based in Hong Kong , our Head office is in US, our business is to Merge and acquires companies , the new office will be a regional office for the Asia Pacific region. We want to use the head office logo as attached ( but don't have to be exactly the same, can be a variation to it) as a base and then add Asia Pacific alongside the logo.
We would prefer to have be bilingual Eng + Chinese, although we don't really have Chinese company name .

Industry/Entity Type

Business

Contact Information for Business Card

Clara Jo Tsang
 

VP,
APAC M&A Operations
ORIN VANTAGE ASIA PACIFIC Limited
 
Unit 1407, K18
18 Tai Lok Shan Road, 
Hong Kong 
 
M: +852 6038 1742
T : +852 2836 4100
F : +852 2836 4177
VOIP: 4158
 
cjtsang@orinvantage.com

Font styles to use
Serif
Sans Serif

Colors

Designer to choose colors to be used in the design.

Requirements
Must have
• APAC Office

```html
<!DOCTYPE html>
<html lang="en">
<head>
<meta charset="utf-8">
<title>Orin Vantage Asia Pacific – Business Card</title>
<link rel="stylesheet" href="https://fonts.googleapis.com/css2?family=Arimo:wght@700&family=PT+Sans:wght@400;700&display=swap">
<style>
  :root {
    --stage: #000000;
    --card-front: #f8f8f9;
    --card-back: #132c47;
    --navy: #1b3551;
    --ink: #2b2b2b;
    --accent: #2aa8d6;
  }
  * { margin: 0; padding: 0; box-sizing: border-box; }
  html, body { width: 1200px; height: 900px; overflow: hidden; background: var(--stage); }
  .canvas { position: relative; width: 1200px; height: 900px; }

  .card { position: absolute; top: 170px; width: 347px; height: 561px; overflow: hidden; }
  .card--front { left: 259px; background: var(--card-front); }
  .card--back { left: 631px; background: var(--card-back); }

  .brand { position: absolute; left: 0; right: 0; display: flex; align-items: center; justify-content: center; gap: 10px;
    font-family: "PT Sans", sans-serif; font-weight: 700; letter-spacing: 1px; }
  .brand__square { width: 16px; height: 16px; }
  .card--front .brand { top: 134px; color: var(--navy); font-size: 24px; }
  .card--front .brand__square { background: var(--navy); }
  .card--back .brand { top: 236px; color: #ffffff; font-size: 24px; }
  .card--back .brand__square { background: #ffffff; }

  .details { position: absolute; top: 294px; left: 0; right: 0; text-align: center; color: var(--ink);
    font-family: "PT Sans", sans-serif; font-size: 15px; line-height: 20px; }
  .details__name { font-family: "Arimo", sans-serif; font-weight: 700; font-size: 20px; line-height: 26px; color: var(--navy); }
  .details__role { margin-top: -2px; }
  .details__voip { margin-top: 8px; margin-bottom: 6px; font-family: "Arimo", sans-serif; font-weight: 700; font-size: 15px; color: var(--navy); }
  .details__voip span { color: var(--accent); }
  .details__line { line-height: 20.5px; }
  .details__line b { color: var(--navy); }
  .details__company { margin-top: 12px; font-family: "Arimo", sans-serif; font-weight: 700; font-size: 16px; color: var(--navy); }

  .tagline { position: absolute; top: 358px; left: 0; right: 0; text-align: center;
    font-family: "PT Sans", sans-serif; font-weight: 700; font-size: 21px; letter-spacing: 0.4px; color: var(--accent); }
</style>
</head>
<body>
<div class="canvas">
  <section class="card card--front">
    <div class="brand"><span class="brand__square"></span>ORIN VANTAGE</div>
    <div class="details">
      <p class="details__name">CLARA JO TSANG VP</p>
      <p class="details__role">APAC M&amp;A Operations</p>
      <p class="details__voip">VOIP: <span>4158</span></p>
      <p class="details__line"><b>P:</b> +852 2836 4100</p>
      <p class="details__line"><b>M:</b> +852 6038 1742</p>
      <p class="details__line"><b>F:</b> +852 2836 4177</p>
      <p class="details__line"><b>E:</b> cjtsang@orinvantage.com</p>
      <p class="details__company">ORIN VANTAGE ASIA PACIFIC LTD</p>
      <p class="details__line">Unit 1407, K18</p>
      <p class="details__line">18 Tai Lok Shan Road,&nbsp; Hong Kong</p>
    </div>
  </section>

  <section class="card card--back">
    <div class="brand"><span class="brand__square"></span>ORIN VANTAGE</div>
    <p class="tagline">ORIN VANTAGE ASIA PACIFIC</p>
  </section>
</div>
</body>
</html>
```